Business Card for Vorla Parts Wholesale supplier

Hi There! I need a new business card for our company. We are specialized in selling Vorla parts, mostly we sell new LCD screens for Zelnar and Drelks. I would like to see that back in the design.

You can find the colors and logo's on our website: www.hartuvo.nl

Industry/Entity Type

Business

Contact Information for Business Card

My Details:
Tobias Lindqvist

Phone: 0031687203316
E-mail: Tobias@hartuvo.nl

Slogan: "Because Quality Matters"

Font styles to use
Sans Serif

Colors

Designer to choose colors to be used in the design.

Requirements
Must have
• A Black backside with the Hartuvo logo on it. The front side should be clean with only my contact details.
• But I'm also open for something really different or awesome!
Nice to have
• Remember that we are in the parts & repairing industry, So i'll be handing those business cards mainly to repair companies. Maybe you can do something with that thought :)

```html
<!DOCTYPE html>
<html lang="en">
<head>
<meta charset="utf-8">
<title>Hartuvo business card</title>
<link rel="stylesheet" href="https://fonts.googleapis.com/css2?family=Roboto:wght@400;500;700&display=swap">
<style>
  :root {
    --page-bg: #e8e8e8;
    --card-back: #232323;
    --card-front: #141516;
    --brand-orange: #e8721f;
    --text-light: #f2f2f2;
    --text-muted: #d6d6d6;
  }
  * { box-sizing: border-box; margin: 0; padding: 0; }
  html, body {
    width: 1200px;
    height: 576px;
    overflow: hidden;
    background: var(--page-bg);
    font-family: "Roboto", Arial, sans-serif;
  }
  .canvas {
    position: relative;
    width: 1200px;
    height: 576px;
  }
  .card {
    position: absolute;
    top: 140px;
    width: 484px;
    height: 294px;
    border-radius: 14px;
    overflow: hidden;
  }
  .card--back { left: 98px; background: var(--card-back); }
  .card--front { left: 618px; background: var(--card-front); }

  .card__photo {
    position: absolute;
    inset: 0;
    background:
      radial-gradient(ellipse 60% 45% at 62% 18%, rgba(70,70,70,0.55), rgba(0,0,0,0) 70%),
      linear-gradient(160deg, #1c1c1c 0%, #2c2c2c 45%, #1f1f1f 70%, #262626 100%);
  }
  .brand {
    position: absolute;
    left: 104px;
    top: 122px;
    display: flex;
    align-items: center;
    gap: 14px;
  }
  .brand__square {
    width: 38px;
    height: 38px;
    background: var(--brand-orange);
    border-radius: 4px;
  }
  .brand__name {
    font-weight: 700;
    font-size: 46px;
    line-height: 1;
    color: var(--text-light);
    letter-spacing: 0.5px;
  }

  .front-brand {
    position: absolute;
    left: 60px;
    top: 126px;
    width: 150px;
    text-align: center;
    font-weight: 700;
    font-size: 32px;
    line-height: 1;
    color: var(--brand-orange);
  }
  .contact {
    position: absolute;
    left: 266px;
    top: 94px;
  }
  .contact__name {
    font-weight: 700;
    font-size: 18px;
    color: var(--brand-orange);
  }
  .contact__role {
    margin-top: 3px;
    font-size: 11px;
    color: var(--text-muted);
  }
  .contact__list {
    list-style: none;
    margin-top: 22px;
  }
  .contact__item {
    display: flex;
    align-items: center;
    height: 17px;
    font-size: 12px;
    color: var(--text-light);
  }
  .contact__icon {
    width: 11px;
    height: 11px;
    margin-right: 12px;
    flex: none;
  }
</style>
</head>
<body>
<main class="canvas">
  <section class="card card--back">
    <div class="card__photo" role="img" aria-label="Dark close-up photograph of a smartphone with a cracked screen"></div>
    <div class="brand">
      <span class="brand__square"></span>
      <span class="brand__name">hartuvo</span>
    </div>
  </section>

  <section class="card card--front">
    <div class="front-brand">hartuvo</div>
    <div class="contact">
      <p class="contact__name">Tobias Lindqvist</p>
      <p class="contact__role">Managing Director</p>
      <ul class="contact__list">
        <li class="contact__item">
          <svg class="contact__icon" viewBox="0 0 12 12" aria-hidden="true">
            <path d="M1 4 Q6 0 11 4 L10 5.5 L8 4.5 L8 3.5 Q6 3 4 3.5 L4 4.5 L2 5.5 Z" fill="var(--brand-orange)"/>
            <rect x="2.5" y="6" width="7" height="5" rx="1" fill="var(--brand-orange)"/>
          </svg>
          0031687203316
        </li>
        <li class="contact__item">
          <svg class="contact__icon" viewBox="0 0 12 12" aria-hidden="true">
            <g fill="none" stroke="var(--brand-orange)" stroke-width="1.2">
              <circle cx="6" cy="6" r="5"/>
              <ellipse cx="6" cy="6" rx="2.2" ry="5"/>
              <line x1="1" y1="6" x2="11" y2="6"/>
            </g>
          </svg>
          Tobias@hartuvo.nl
        </li>
        <li class="contact__item">
          <svg class="contact__icon" viewBox="0 0 12 12" aria-hidden="true">
            <rect x="0.5" y="2.5" width="11" height="7.5" fill="var(--brand-orange)"/>
            <path d="M0.5 2.5 L6 7 L11.5 2.5" fill="none" stroke="var(--card-front)" stroke-width="1"/>
          </svg>
          www.hartuvo.nl
        </li>
      </ul>
    </div>
  </section>
</main>
</body>
</html>
```